I need a complete stationary pack for a real estate office that sells and manages residential proper

We need a stationary design pack for my real estate office called ‘brightkeyhomes’ that is in Queensland Australia. My offices are both in suburban and coastal locations in the south west corner of Queensland at the Coral Bay Shore and Brisbane.
We predominately manage real estate on behalf of owners and sell property in the residential sector.
I have attached a copy of our existing design of my business card and do like the current concept/layout. In saying this you may be able to use this existing theme across to the other items required or see opportunity on how to improve what I have already.
I would like to see concepts for the following products:
- Letterhead
- Fax header
- Business cards
- Email signature
- With complements slips and
- Envelopes
I have attached our current logo that was designed by Artfolder and the font is Prelo.

I am looking for a contemporary design that is professional and reflects trust and professionalism. I am currently using the logo with a black background on some material as per the following link

http://www.plotlisting.com.au/property/for-sale/house/qld/merridale/?adid=4827305118&sp=7

I have posted another job 517362 for signage and the company car signage done too if you are interested.

Please do not hesitate to contact me should you have any questions. Thank you.

Target Market(s)

Western speaking people aged from 25 to 60 from modest backgrounds to well off individuals

Industry/Entity Type

Real Estate

Requirements
Must have
• Professional in appearance, show a mature and trustworthy image
Should not have
• As there is good colour with the logo, i am do not want over the top designs or colours

```html
<!DOCTYPE html>
<html lang="en">
<head>
<meta charset="utf-8">
<title>brightkeyhomes – Business Cards</title>
<link href="https://fonts.googleapis.com/css2?family=Open+Sans:wght@400;600;700&display=swap" rel="stylesheet">
<style>
  :root {
    --page-bg: #ecebe8;
    --navy-dark: #1f2a3a;
    --navy-mid: #2b3a4f;
    --card-white: #ffffff;
    --ink: #4a4f57;
    --ink-soft: #6b7079;
    --red: #e0353b;
    --blue: #1f7fc4;
    --green: #3aa346;
    --purple: #7b3f98;
    --orange: #f39a1f;
  }
  * { box-sizing: border-box; margin: 0; padding: 0; }
  html, body {
    width: 1200px; height: 1024px; overflow: hidden;
    background: var(--page-bg);
    font-family: "Open Sans", Arial, sans-serif;
  }
  .sheet {
    width: 1200px; height: 1024px;
    display: flex; flex-direction: column; align-items: center; justify-content: center;
    gap: 60px;
  }
  .card {
    position: relative;
    width: 640px; height: 390px;
    border-radius: 26px;
    overflow: hidden;
    box-shadow: 0 10px 28px rgba(0,0,0,0.18);
  }

  /* Front */
  .card-front {
    background: radial-gradient(ellipse at 50% 45%, var(--navy-mid) 0%, var(--navy-dark) 75%);
    display: flex; align-items: center; justify-content: center; gap: 18px;
  }
  .brand-dot {
    width: 64px; height: 64px; border-radius: 50%;
    background: var(--orange);
  }
  .brand-name-front {
    color: #ffffff;
    font-weight: 600;
    font-size: 46px;
    letter-spacing: -0.5px;
  }

  /* Back */
  .card-back { background: var(--card-white); }
  .back-brand {
    position: absolute; left: 44px; top: 128px;
    display: flex; align-items: center; gap: 12px;
  }
  .back-brand .brand-dot { width: 40px; height: 40px; }
  .brand-name-back {
    color: var(--ink);
    font-weight: 600;
    font-size: 30px;
    letter-spacing: -0.4px;
  }
  .contact {
    position: absolute; left: 360px; top: 46px;
    color: var(--ink-soft);
  }
  .contact-name { color: var(--red); font-weight: 700; font-size: 24px; line-height: 1.15; }
  .contact-role { color: var(--blue); font-weight: 600; font-size: 19px; line-height: 1.2; }
  .contact-mobile { font-size: 14px; margin-top: 4px; margin-bottom: 10px; }
  .contact-list { list-style: none; }
  .contact-list li {
    display: flex; align-items: flex-start; gap: 8px;
    font-size: 13.5px; line-height: 1.35; margin-bottom: 3px;
  }
  .contact-list svg { flex: none; width: 14px; height: 14px; margin-top: 2px; }
  .accent-band {
    position: absolute; left: 0; bottom: 0;
    width: 640px; height: 110px;
    background: linear-gradient(90deg, #5fae8a 0%, #5b8fc4 35%, #8a6aa8 65%, #d9646a 100%);
    opacity: 0.85;
  }
</style>
</head>
<body>
<main class="sheet">

  <section class="card card-front" aria-label="Business card front">
    <span class="brand-dot"></span>
    <span class="brand-name-front">brightkeyhomes</span>
  </section>

  <section class="card card-back" aria-label="Business card back">
    <div class="back-brand">
      <span class="brand-dot"></span>
      <span class="brand-name-back">brightkeyhomes</span>
    </div>

    <div class="contact">
      <p class="contact-name">Marcus Hallor</p>
      <p class="contact-role">Principal</p>
      <p class="contact-mobile">0427581946</p>
      <ul class="contact-list">
        <li>
          <svg viewBox="0 0 14 14"><path d="M7 1a4 4 0 0 0-4 4c0 3 4 8 4 8s4-5 4-8a4 4 0 0 0-4-4z" fill="var(--green)"/><circle cx="7" cy="5" r="1.5" fill="#fff"/></svg>
          <span>shop 4, 212 harbour way,<br>merridale qld 4581</span>
        </li>
        <li>
          <svg viewBox="0 0 14 14"><circle cx="7" cy="7" r="7" fill="var(--green)"/><path d="M4.5 3.5l1.5 0 .6 2-1 .8a5 5 0 0 0 2.1 2.1l.8-1 2 .6 0 1.5c-3.5.4-6.4-2.5-6-6z" fill="#fff"/></svg>
          <span>07 5492 6170</span>
        </li>
        <li>
          <svg viewBox="0 0 14 14"><circle cx="7" cy="7" r="7" fill="var(--green)"/><rect x="3.5" y="4.5" width="7" height="5" fill="#fff"/><path d="M3.5 4.5l3.5 3 3.5-3" stroke="var(--green)" stroke-width="0.8" fill="none"/></svg>
          <span>marcus@brightkeyhomes.com.au</span>
        </li>
        <li>
          <svg viewBox="0 0 14 14"><circle cx="7" cy="7" r="7" fill="var(--green)"/><circle cx="7" cy="7" r="4" fill="none" stroke="#fff" stroke-width="1"/><path d="M3 7h8M7 3v8" stroke="#fff" stroke-width="0.8"/></svg>
          <span>www.brightkeyhomes.com.au</span>
        </li>
      </ul>
    </div>

    <div class="accent-band" role="img" aria-label="Decorative colour band along the bottom edge of the card"></div>
  </section>

</main>
</body>
</html>
```